Cyber Security Site Design (Products & Consulting)

I need my website redesigned to be engaging, clean, efficient and modern. My company (when its up and running) is going to be concentrated on two things: a few specific products for cyber security as well as cyber security consulting services. The background I bring to the field is having worked with small companies all the way to the largest government organizations and advising them on their security posture and how to improve it. We need the ability to add products and services easily.

For a sample product, you can use either Tarnet (http://www.tarnet-relay.org/) or Verodyne Ashmantle (https://www.verodyne.com/products/relay-hx-and-fortified-edge-portal).

It will replace https://lumerafieldworks.com/

Target Market(s)

Cyber Security professionals in all verticals

Coding

Coded - Design and coding required

Number of Pages Required

4 page

Font styles to use
Sans Serif

Colors
6b449b

Requirements
Must have
• Ability to easily modify
• Have main page
• Have product specific pages
• Have consulting services pages
• Have executive team information
• Clean, modern design
• Usage of the logo and its color scheme
Nice to have
• I like the idea of a left collapsed sidebar (so icons only) that can expand for text.
• I am also open to a very unique landing page, possibly a shape in the middle (hexagons maybe?) with each of the options there.
Should not have
• Nothing that looks like it came out of a hacker movie

```html
<!DOCTYPE html>
<html lang="en">
<head>
<meta charset="utf-8">
<title>Lumera Fieldworks — Cyber Security Products &amp; Consulting</title>
<link rel="stylesheet" href="https://fonts.googleapis.com/css2?family=Aldrich&family=Oswald:wght@500;600&family=Mulish:wght@400;600;700;800&display=swap">
<style>
:root{
  --purple:#6b449b;
  --purple-dark:#4f2f7a;
  --purple-soft:#8a63bd;
  --ink:#1f1f2a;
  --text:#55555f;
  --muted:#8a8a94;
  --light:#f4f4f7;
  --line:#e3e3ea;
  --white:#ffffff;
  --orange:#f2913a;
  --night:#1c2330;
}
*{box-sizing:border-box;margin:0;padding:0}
html,body{width:1200px;height:4500px;overflow:hidden}
body{position:relative;background:var(--white);font-family:"Mulish",Arial,sans-serif;color:var(--text)}
.abs{position:absolute}
.section-title{position:absolute;left:0;width:1200px;text-align:center;font-family:"Aldrich",sans-serif;font-size:34px;color:var(--ink);letter-spacing:1px}
.title-mark{position:absolute;left:588px;width:24px;height:24px}

/* header */
.site-header{position:absolute;left:0;top:0;width:1200px;height:114px;background:var(--white)}
.brand{position:absolute;left:105px;top:22px;display:flex;align-items:center;gap:14px}
.brand-dot{width:58px;height:58px;border-radius:50%;background:var(--purple)}
.brand-name{font-family:"Mulish",sans-serif;font-weight:800;font-size:32px;color:var(--purple);line-height:1;letter-spacing:1px}
.contact-item{position:absolute;top:20px;display:flex;align-items:center;gap:8px;font-size:13px;color:var(--ink);white-space:nowrap}
.round-ico{width:24px;height:24px;border-radius:50%;background:var(--purple);display:inline-block}
.socials{position:absolute;top:18px;left:1000px;display:flex;gap:5px}
.socials i{width:24px;height:24px;border-radius:50%;background:var(--purple);display:block}
.main-nav{position:absolute;top:80px;left:594px;display:flex;gap:46px;font-size:14px;font-weight:600;color:var(--ink)}
.main-nav .active{color:var(--purple);border-bottom:3px solid var(--purple);padding-bottom:10px}

/* hero */
.hero{position:absolute;left:0;top:114px;width:1200px;height:549px;background:linear-gradient(120deg,#3b4a63 0%,#6f86a8 45%,#c9d6e6 70%,#8da2bf 100%)}
.hero-text{position:absolute;left:144px;top:176px;font-family:"Oswald",sans-serif;font-weight:600;font-size:40px;line-height:52px;color:var(--white);width:400px}
.hero-arrow{position:absolute;top:258px;width:34px;height:34px;border-radius:50%;background:rgba(255,255,255,.85)}

/* about */
.about-text{position:absolute;left:180px;top:810px;width:840px;text-align:center;font-size:15px;line-height:28px;color:var(--text)}

/* services */
.services{position:absolute;left:0;top:990px;width:1200px;height:705px;background:var(--light)}
.service{position:absolute;width:282px;height:210px;text-align:center;padding-top:24px}
.service svg{width:60px;height:60px}
.service h3{font-family:"Mulish",sans-serif;font-size:15px;font-weight:700;color:var(--ink);margin:12px 0 6px}
.service p{font-size:13px;line-height:20px;color:var(--text);padding:0 24px}
.service.featured{background:var(--purple);border-radius:4px}
.service.featured h3,.service.featured p{color:var(--white)}
.grid-line{position:absolute;background:var(--line)}

/* products */
.product{position:absolute;top:1875px;width:441px;height:252px;background:var(--white);box-shadow:0 2px 14px rgba(0,0,0,.08);border-radius:4px}
.box-art{position:absolute;left:30px;top:30px;width:150px;height:192px}
.product h3{position:absolute;left:204px;top:36px;font-family:"Aldrich",sans-serif;font-size:24px;color:var(--purple)}
.product p{position:absolute;left:204px;top:76px;width:215px;font-size:13px;line-height:20px}
.product a{position:absolute;left:204px;top:190px;font-size:14px;color:var(--purple);text-decoration:none}

/* security cta */
.cta{position:absolute;left:0;top:2205px;width:1200px;height:425px;background:var(--light)}
.cta-art{position:absolute;left:156px;top:75px;width:288px;height:282px;border-radius:50% 0 50% 50%;background:linear-gradient(135deg,#e6e1ee,#9fa8b8 60%,#4a5568)}
.cta h2{position:absolute;left:492px;top:93px;font-family:"Aldrich",sans-serif;font-size:29px;color:var(--ink)}
.cta h4{position:absolute;left:492px;top:138px;font-size:18px;font-weight:700;color:var(--ink)}
.cta p{position:absolute;left:492px;top:180px;width:600px;font-size:13px;line-height:22px}
.btn{position:absolute;display:flex;align-items:center;background:var(--purple);color:var(--white);font-weight:700;font-size:15px;letter-spacing:1px;height:42px;padding:0 22px 0 54px}
.btn::before{content:"";position:absolute;left:-6px;top:-4px;width:50px;height:50px;border-radius:50%;background:var(--ink)}

/* team */
.member{position:absolute;top:2835px;width:216px;height:222px;background:var(--white);border:1px solid var(--line);text-align:center}
.avatar{width:108px;height:108px;border-radius:50%;margin:24px auto 18px;background:linear-gradient(160deg,#d9d4e2,#8f86a1)}
.member h3{font-size:15px;font-weight:800;color:var(--ink)}
.member p{font-size:12px;margin-top:5px;color:var(--muted);letter-spacing:.5px}
.pager{position:absolute;top:3078px;width:26px;height:26px;border-radius:50%;border:2px solid var(--line)}

/* stats */
.stats{position:absolute;left:0;top:3177px;width:1200px;height:237px;background:linear-gradient(90deg,var(--purple-dark),var(--purple) 50%,var(--purple-dark))}
.stat{position:absolute;top:36px;width:200px;text-align:center;color:var(--white)}
.stat svg{width:56px;height:56px}
.stat b{display:block;font-family:"Mulish",sans-serif;font-size:50px;font-weight:600;line-height:60px}
.stat span{font-size:15px;font-weight:700;letter-spacing:1px}

/* reviews */
.review{position:absolute;text-align:center;padding:30px 30px}
.review .q{font-size:44px;line-height:30px;color:var(--purple);font-family:Georgia,serif}
.review h4{font-size:16px;font-weight:800;color:var(--purple);margin:6px 0 10px}
.review p{font-size:12px;line-height:20px}
.review .who{margin-top:14px;font-size:12px;font-weight:800;color:var(--ink)}
.review .role{font-size:11px;letter-spacing:1px;color:var(--muted)}
.review.main{left:411px;top:3579px;width:378px;height:246px;background:var(--white);box-shadow:0 4px 20px rgba(0,0,0,.12)}
.review.side{top:3612px;width:300px;opacity:.35}

/* location */
.location{position:absolute;left:0;top:3912px;width:1200px;height:528px;background:linear-gradient(120deg,#141a26,#2b3447 55%,#161c28)}
.location h2{position:absolute;left:228px;top:66px;font-family:"Aldrich",sans-serif;font-size:33px;color:var(--white)}
.location .lead{position:absolute;left:228px;top:114px;width:330px;font-size:15px;line-height:22px;color:#c9cbd3}
.map{position:absolute;left:228px;top:228px;width:432px;height:228px;background:linear-gradient(135deg,#e7e8ea,#cfd3d8)}
.office{position:absolute;left:75px;top:60px;background:var(--white);padding:10px 14px;font-size:11px;font-weight:800;color:var(--ink);box-shadow:0 2px 6px rgba(0,0,0,.2)}
.form{position:absolute;left:660px;top:4035px;width:315px;height:315px;background:var(--white)}
.form h2{position:absolute;left:72px;top:18px;font-family:"Aldrich",sans-serif;font-size:30px;color:var(--purple)}
.form .sub{position:absolute;left:72px;top:60px;font-size:12px;color:var(--text)}
.field{position:absolute;left:72px;width:210px;border-bottom:1px solid var(--line);font-size:12px;color:var(--muted);padding-bottom:6px}
.form .btn{left:48px;top:258px;height:34px;font-size:13px;padding-left:44px}
.form .btn::before{width:40px;height:40px;top:-3px}

.site-footer{position:absolute;left:0;top:4440px;width:1200px;height:60px;background:var(--purple);color:var(--white);font-size:13px;letter-spacing:.5px}
.site-footer p{position:absolute;left:144px;top:22px}
.site-footer .socials{left:930px;top:18px}
.site-footer .socials i{background:var(--white)}
</style>
</head>
<body>

<header class="site-header">
  <div class="brand"><span class="brand-dot"></span><span class="brand-name">LUMERA<br>FIELDWORKS</span></div>
  <span class="contact-item" style="left:555px"><i class="round-ico"></i>(012) 555 0147</span>
  <span class="contact-item" style="left:765px"><i class="round-ico"></i>inquiry@lumerafieldworks.com</span>
  <div class="socials"><i></i><i></i><i></i><i></i></div>
  <nav class="main-nav">
    <span class="active">HOME</span><span>SERVICES</span><span>OUR TEAM</span><span>PRODUCTS</span><span>CONTACT US</span>
  </nav>
</header>

<section class="hero" role="img" aria-label="Photo of a hand placing a jigsaw puzzle piece into a blue puzzle">
  <h1 class="hero-text">We Provide Early Detection, Immediate Remediation &amp; Proactive Preventive Measures</h1>
  <svg class="hero-arrow" style="left:52px" viewBox="0 0 34 34"><path d="M20 10 L13 17 L20 24" stroke="#333" stroke-width="2.5" fill="none"/></svg>
  <svg class="hero-arrow" style="left:1114px" viewBox="0 0 34 34"><path d="M14 10 L21 17 L14 24" stroke="#333" stroke-width="2.5" fill="none"/></svg>
</section>

<h2 class="section-title" style="top:730px">ABOUT US</h2>
<svg class="title-mark" style="top:774px" viewBox="0 0 24 24"><rect x="3" y="3" width="18" height="18" rx="3" fill="none" stroke="var(--purple)" stroke-width="3"/></svg>
<p class="about-text">We are a company that takes its roots from the idea of providing appropriate and creative solutions for cyber security operations, development and management. We have a mission first mindset for our clients and their objectives.<br>We are located in the Brennan Falls / Corvel Ridge area but are able to work with clients world-wide. Please contact us for any inquires you may have and we will be glad to assist you in any way possible.</p>

<section class="services">
  <h2 class="section-title" style="top:66px">CYBER SECURITY CONSULTING SERVICES</h2>
  <svg class="title-mark" style="top:110px" viewBox="0 0 24 24"><rect x="3" y="3" width="18" height="18" rx="3" fill="none" stroke="var(--purple)" stroke-width="3"/></svg>
  <div class="grid-line" style="left:159px;top:393px;width:882px;height:1px"></div>
  <div class="grid-line" style="left:444px;top:405px;width:1px;height:210px"></div>
  <div class="grid-line" style="left:756px;top:405px;width:1px;height:210px"></div>

  <div class="service" style="left:159px;top:171px">
    <svg viewBox="0 0 60 60" fill="none" stroke="var(--purple)" stroke-width="2"><circle cx="30" cy="20" r="10"/><path d="M12 52c2-12 10-18 18-18s16 6 18 18"/></svg>
    <h3>VIRTUAL CISO / VISO</h3><p>Adipiscing elit sed autelt eiusmodte mporal laboratories dolore magna aliqua renim adim minim veniam quis.</p></div>
  <div class="service featured" style="left:459px;top:171px">
    <svg viewBox="0 0 60 60" fill="none" stroke="#fff" stroke-width="2"><rect x="18" y="18" width="24" height="24"/><path d="M24 10v8M36 10v8M24 42v8M36 42v8M10 24h8M10 36h8M42 24h8M42 36h8"/></svg>
    <h3>CYBER SECURITY</h3><p>Adipiscing elit sed autelt eiusmodte mporal laboratories dolore magna aliqua renim adim minim veniam quis.</p></div>
  <div class="service" style="left:759px;top:171px">
    <svg viewBox="0 0 60 60" fill="none" stroke="var(--purple)" stroke-width="2"><circle cx="26" cy="26" r="14"/><path d="M36 36l14 14"/><path d="M26 19v9M26 32v2"/></svg>
    <h3>INCIDENT RESPONSE</h3><p>Adipiscing elit sed autelt eiusmodte mporal laboratories dolore magna aliqua renim adim minim veniam quis.</p></div>
  <div class="service" style="left:159px;top:408px">
    <svg viewBox="0 0 60 60" fill="none" stroke="var(--purple)" stroke-width="2"><circle cx="30" cy="16" r="6"/><circle cx="14" cy="40" r="6"/><circle cx="46" cy="40" r="6"/><path d="M30 22v10M18 36l12-4 12 4"/></svg>
    <h3>RISK ASSESSMENT</h3><p>Adipiscing elit sed autelt eiusmodte mporal laboratories dolore magna aliqua renim adim minim veniam quis.</p></div>
  <div class="service" style="left:459px;top:408px">
    <svg viewBox="0 0 60 60" fill="none" stroke="var(--purple)" stroke-width="2"><path d="M30 8l18 7v14c0 12-8 20-18 23-10-3-18-11-18-23V15z"/><circle cx="30" cy="30" r="6"/></svg>
    <h3>NETWORK SECURITY</h3><p>Adipiscing elit sed autelt eiusmodte mporal laboratories dolore magna aliqua renim adim minim veniam quis.</p></div>
  <div class="service" style="left:759px;top:408px">
    <svg viewBox="0 0 60 60" fill="none" stroke="var(--purple)" stroke-width="2"><rect x="8" y="12" width="44" height="30" rx="2"/><path d="M22 50h16M30 42v8M23 27l5 5 9-10"/></svg>
    <h3>MANAGED SECURITY SERVICES</h3><p>Adipiscing elit sed autelt eiusmodte mporal laboratories dolore magna aliqua renim adim minim veniam quis.</p></div>
</section>

<h2 class="section-title" style="top:1762px">PRODUCTS</h2>
<svg class="title-mark" style="top:1806px" viewBox="0 0 24 24"><rect x="3" y="3" width="18" height="18" rx="3" fill="none" stroke="var(--purple)" stroke-width="3"/></svg>
<article class="product" style="left:144px">
  <div class="box-art" role="img" aria-label="Product box for a cyber security product" style="background:linear-gradient(160deg,#f2f2f2 40%,#2fb5b0 40%,#1d8f9a)"></div>
  <h3>PRODUCT 1</h3>
  <p>Morbi convallis bibendum urna ut viverra. Maecenas quis consequat libero, a feugiat eros. Nunc ut lacinia tortor morbi ultricies laoreet ullamcorper phasellus semper.</p>
  <a href="#">View Details →</a>
</article>
<article class="product" style="left:624px">
  <div class="box-art" role="img" aria-label="Product box for a cyber security product" style="background:linear-gradient(160deg,#f2f2f2 40%,#f4c430 40%,#e0a800)"></div>
  <h3>PRODUCT 2</h3>
  <p>Morbi convallis bibendum urna ut viverra. Maecenas quis consequat libero, a feugiat eros. Nunc ut lacinia tortor morbi ultricies laoreet ullamcorper phasellus semper.</p>
  <a href="#">View Details →</a>
</article>

<section class="cta">
  <div class="cta-art" role="img" aria-label="Photo of a team meeting around an office table"></div>
  <h2>YOU NEED MORE SECURITY?</h2>
  <h4>Aliquam sapien est, mollis id mattis id, scelerisque sed dolor.</h4>
  <p>Proin accumsan erat sem, id porta risus dignissim ac. Vestibulum nec sapien in lacus ornare nec nec justo. Aliquam sapien est, mollis id mattis id, scelerisque sed dolor. Proin accumsan erat sem, id porta risus dignissim ac. Vestibulum nec sapien in lacus ornare nec nec justo.</p>
  <a class="btn" style="left:510px;top:282px">CONTACT US TODAY</a>
</section>

<h2 class="section-title" style="top:2738px">OUR TEAM</h2>
<svg class="title-mark" style="top:2782px" viewBox="0 0 24 24"><rect x="3" y="3" width="18" height="18" rx="3" fill="none" stroke="var(--purple)" stroke-width="3"/></svg>
<div class="member" style="left:144px"><div class="avatar" role="img" aria-label="Portrait of team member"></div><h3>Marcus Delavane Whitcombe</h3><p>Founder &amp; CEO</p></div>
<div class="member" style="left:375px"><div class="avatar" role="img" aria-label="Portrait of team member"></div><h3>Helena Marchetti</h3><p>ASSOCIATE</p></div>
<div class="member" style="left:606px"><div class="avatar" role="img" aria-label="Portrait of team member"></div><h3>Tobias Kerrigan</h3><p>NISLLACUS</p></div>
<div class="member" style="left:843px"><div class="avatar" role="img" aria-label="Portrait of team member"></div><h3>Iris Calloway</h3><p>NISLLACUS</p></div>
<span class="pager" style="left:570px"></span>
<span class="pager" style="left:603px;border-color:var(--ink)"></span>

<section class="stats">
  <div class="stat" style="left:111px"><svg viewBox="0 0 56 56" fill="none" stroke="var(--orange)" stroke-width="2"><circle cx="20" cy="18" r="7"/><circle cx="38" cy="18" r="7"/><path d="M6 44c2-10 8-14 14-14s12 4 14 14M24 44c2-10 8-14 14-14s12 4 14 14"/></svg><b>120</b><span>ABOUT EMPLOYEE</span></div>
  <div class="stat" style="left:384px"><svg viewBox="0 0 56 56" fill="var(--orange)"><rect x="8" y="30" width="8" height="18"/><rect x="20" y="22" width="8" height="26"/><rect x="32" y="14" width="8" height="34"/><rect x="44" y="8" width="6" height="40"/></svg><b>250</b><span>QUERIES SOLVED</span></div>
  <div class="stat" style="left:612px"><svg viewBox="0 0 56 56" fill="none" stroke="var(--orange)" stroke-width="2"><circle cx="28" cy="28" r="22"/><circle cx="28" cy="22" r="8"/><path d="M14 44c4-8 8-10 14-10s10 2 14 10"/></svg><b>550</b><span>REGISTERED USERS</span></div>
  <div class="stat" style="left:855px"><svg viewBox="0 0 56 56" fill="none" stroke="var(--orange)" stroke-width="2"><circle cx="28" cy="28" r="22"/><circle cx="20" cy="22" r="2" fill="var(--orange)"/><circle cx="36" cy="22" r="2" fill="var(--orange)"/><path d="M18 34c4 6 16 6 20 0"/></svg><b>1000</b><span>HAPPY CUSTOMERS</span></div>
</section>

<h2 class="section-title" style="top:3472px">CUSTOMER REVIEWS</h2>
<div class="review side" style="left:120px"><div class="q">“</div><h4>Lorem Ipsum Dolor Sit Amet</h4><p>Ut enim ad minim veniam dolor siteme magnanth ab consectetur adipiscing expedita.</p><p class="who">Harlan Voss, Quietmere</p><p class="role">NISI ELEMENTUM</p></div>
<div class="review side" style="left:780px"><div class="q">“</div><h4>Lorem Ipsum Dolor Sit</h4><p>Ut enim ad minim veniam dolor siteme magnanth ab consectetur adipiscing expedita.</p><p class="who">Corin Pell, Ashbrook</p><p class="role">NISI ELEMENTUM</p></div>
<div class="review main"><div class="q">“</div><h4>Lorem Ipsum Dolor Sit Amet ...</h4><p>Ut enim ad minim veniam dolor siteme magnanth ab consectetur adipiscing. Expedita animo maiores aliquid hic ab dolorem aut fuepe voluptates pariatur aut et repellat. Quo quo voluptas ncididunt ameitfit consectetur sunt laudantium est et.</p><p class="who">Delia Rourke, Orvanta</p><p class="role">QUODIG VULPUTAT</p></div>

<section class="location">
  <h2>OUR LOCATION</h2>
  <p class="lead">Aliquam sapien est, mollis id mattis id, scelerisque sed dolor proin accumsan erat sem.</p>
  <div class="map" role="img" aria-label="Street map showing the corporate office location">
    <div class="office">CORPORATE OFFICE<br><span style="font-weight:600;color:var(--purple)">GET A DIRECTION</span></div>
    <svg class="abs" style="left:260px;top:45px" width="26" height="36" viewBox="0 0 26 36"><path d="M13 0C6 0 0 6 0 13c0 9 13 23 13 23s13-14 13-23C26 6 20 0 13 0z" fill="#e53935"/><circle cx="13" cy="13" r="5" fill="#fff"/></svg>
  </div>
</section>
<div class="form">
  <h2>NEED HELP?</h2>
  <p class="sub">Fill out the form below to get connected</p>
  <div class="field" style="top:96px">Name *</div>
  <div class="field" style="top:132px">Email *</div>
  <div class="field" style="top:168px">Subject *</div>
  <div class="field" style="top:204px">Message *</div>
  <a class="btn">SUBMIT</a>
</div>

<footer class="site-footer">
  <p>COPYRIGHT © 2018 LUMERA FIELDWORKS. ALL RIGHTS RESERVED.</p>
  <div class="socials"><i></i><i></i><i></i><i></i></div>
</footer>

</body>
</html>
```